I am looking for a modern, clean and neat design for a reflexology and well being business. The business name is Gralo Tund (this is an old Latin word for wellbeing). The colours I would like are purple, white and grey. I am open to suggestions for pictures such as healing or working hands, a pair of feet, images that represent my business that you may think of....... or maybe you think no images at all would be best? My tag line is: "Relax, Renew, Revive" or "Find you balance......... Relax, Renew, Revive" I can decide which I want so I would like to see what both would look like. I would like space on the back to write the client's appointment date and time (more than once)

```html
<!DOCTYPE html>
<html lang="en">
<head>
<meta charset="utf-8">
<title>Gralo Tund – Business Card</title>
<link href="https://fonts.googleapis.com/css2?family=Open+Sans:wght@400;600;700&family=Roboto:wght@700&family=Libre+Baskerville&display=swap" rel="stylesheet">
<style>
  :root {
    --backdrop: #e9e6e8;
    --magenta-top: #ee0ae8;
    --magenta-bottom: #c21cd4;
    --brand: #d41ed8;
    --brand-deep: #b51fd0;
    --ink: #3a3a3a;
    --grey-ring: #444;
    --white: #ffffff;
  }
  * { box-sizing: border-box; margin: 0; padding: 0; }
  html, body { width: 1200px; height: 900px; overflow: hidden; }
  body { background: var(--backdrop); position: relative; font-family: "Open Sans", sans-serif; }

  .card { position: absolute; overflow: hidden; box-shadow: 0 6px 18px rgba(0,0,0,.18); }

  /* Front */
  .card-front {
    left: 238px; top: 62px; width: 555px; height: 342px;
    background: linear-gradient(180deg, var(--magenta-top), var(--magenta-bottom));
    color: var(--white);
  }
  .front-badge { position: absolute; left: 265px; top: -7px; width: 360px; height: 360px;
    border-radius: 50%; background: var(--white); }
  .front-badge-name { position: absolute; left: 0; top: 150px; width: 360px; text-align: center;
    font-weight: 700; font-size: 38px; color: var(--brand-deep); padding-right: 90px; }
  .holder-name { position: absolute; left: 26px; top: 34px; font-weight: 700; font-size: 18px; text-transform: uppercase; }
  .holder-role { position: absolute; left: 26px; top: 61px; font-size: 14.5px; }
  .address { position: absolute; left: 24px; top: 182px; font-size: 14.5px; line-height: 20px; }
  .contacts { position: absolute; left: 24px; top: 243px; list-style: none; font-size: 14.5px; line-height: 20.5px; }
  .contacts li { display: flex; align-items: center; gap: 9px; }
  .contacts svg { width: 11px; height: 11px; fill: var(--white); }

  /* Back */
  .card-back {
    left: 457px; top: 519px; width: 560px; height: 342px;
    background: var(--white); text-align: center;
  }
  .back-dot { position: absolute; left: 250px; top: 24px; width: 60px; height: 60px;
    border-radius: 50%; border: 3px solid var(--brand); }
  .brand-name { position: absolute; left: 0; right: 0; top: 92px;
    font-family: "Roboto", sans-serif; font-weight: 700; font-size: 42px; color: var(--brand); }
  .tagline { position: absolute; left: 0; right: 0; top: 141px;
    font-family: "Libre Baskerville", serif; font-size: 12.5px; letter-spacing: 2.4px; color: var(--ink); text-transform: uppercase; }
  .appt-title { position: absolute; left: 0; right: 0; top: 163px; font-weight: 600; font-size: 21.5px; color: var(--brand); }
  .appt-field { position: absolute; display: flex; align-items: baseline; font-weight: 600; font-size: 16px; color: var(--brand); }
  .appt-field .line { display: inline-block; border-bottom: 2px dotted var(--brand); height: 14px; margin-left: 6px; }
  .field-name { left: 70px; top: 205px; }
  .field-date { left: 70px; top: 253px; }
  .field-date .ampm { font-weight: 400; margin-left: 6px; }
  .notice { position: absolute; left: 0; right: 0; top: 292px; font-weight: 600; font-size: 16.5px; color: var(--brand); }
</style>
</head>
<body>

<section class="card card-front">
  <div class="front-badge"><div class="front-badge-name">Gralo Tund</div></div>
  <div class="holder-name">Mara Vellin</div>
  <div class="holder-role">Managing Director</div>
  <div class="address">42, Linden Row<br>Westvale, 204518.</div>
  <ul class="contacts">
    <li><svg viewBox="0 0 24 24"><path d="M6.6 10.8a15.1 15.1 0 0 0 6.6 6.6l2.2-2.2c.3-.3.7-.4 1-.2 1.1.4 2.3.6 3.6.6.6 0 1 .4 1 1V20c0 .6-.4 1-1 1A17 17 0 0 1 3 4c0-.6.4-1 1-1h3.5c.6 0 1 .4 1 1 0 1.3.2 2.5.6 3.6.1.3 0 .7-.2 1z"/></svg>044-555 010 234</li>
    <li><svg viewBox="0 0 24 24"><path d="M2 5h20v14H2zm2 2v.5l8 5 8-5V7z"/></svg>hello@gralotund.com</li>
    <li><svg viewBox="0 0 24 24"><circle cx="12" cy="12" r="10"/></svg>www.gralotund.com</li>
  </ul>
</section>

<section class="card card-back">
  <div class="back-dot"></div>
  <div class="brand-name">Gralo Tund</div>
  <div class="tagline">Relax, Renew, Revive</div>
  <div class="appt-title">Your Next Appointment on</div>
  <div class="appt-field field-name">Name :<span class="line" style="width:345px"></span></div>
  <div class="appt-field field-date">Date :<span class="line" style="width:122px"></span>
    <span style="margin-left:12px">Time :</span><span class="line" style="width:108px"></span><span class="ampm">AM / PM</span></div>
  <div class="notice">If unable to keep appointment, kindly give 24hrs notice.</div>
</section>

</body>
</html>
```